Request for Business Card Design

Hi. My name is Marlene, I am looking for a new business card design for my company, Quarrow Signal Instruments, LLC. I really like the design you did for Tarsel Venture and was hoping you could do something similar using our full logo and our mark. I am also open to any raised texture design using our mark. I have attached our full logo, which would need to be somewhere on the card, as well as the mark in both outline and full form, as well as our brand colors / guide. The card does not have to be white, as long as our logo and mark appear. I actually like darker colored business cards more, but am open to all options. If you are interested in working with me, please let me know. We would also take the business card design into letterhead design if you can do that.

```html
<!DOCTYPE html>
<html lang="en">
<head>
<meta charset="utf-8">
<title>Quarrow Signal Instruments – Business Card</title>
<link rel="stylesheet" href="https://fonts.googleapis.com/css2?family=Open+Sans:wght@400;600;700&display=swap">
<style>
  :root {
    --backdrop: #3a3a3a;
    --card: #141414;
    --card-edge: #1aa0d2;
    --accent: #1aa0d2;
    --ink: #f2f2f2;
    --ink-soft: #d6d6d6;
  }
  * { box-sizing: border-box; margin: 0; padding: 0; }
  html, body {
    width: 1200px; height: 801px; overflow: hidden;
    background: var(--backdrop);
    font-family: "Open Sans", Arial, sans-serif;
  }
  .stage {
    position: relative; width: 1200px; height: 801px;
    display: flex; align-items: center; justify-content: center; gap: 48px;
  }
  .card {
    position: relative; width: 525px; height: 300px;
    background: var(--card);
    border-bottom: 3px solid var(--card-edge);
    overflow: hidden;
  }
  /* Front */
  .brand {
    position: absolute; left: 200px; top: 52px;
    display: flex; align-items: center; gap: 12px;
  }
  .brand-dot { width: 30px; height: 30px; border-radius: 50%; background: var(--accent); }
  .brand-name {
    font-weight: 700; font-size: 34px; letter-spacing: 2px; color: var(--ink); line-height: 1;
  }
  .brand-tagline {
    position: absolute; left: 243px; top: 92px;
    font-size: 8px; font-weight: 600; letter-spacing: 0.6px; color: var(--ink);
    text-transform: uppercase;
  }
  .divider {
    position: absolute; left: 28px; right: 0; top: 150px;
    height: 1px; background: var(--accent);
  }
  .address {
    position: absolute; right: 26px; top: 120px; text-align: right;
    font-size: 11px; line-height: 15px; color: var(--ink);
  }
  .holder { position: absolute; left: 28px; top: 170px; }
  .holder-name {
    font-weight: 600; font-size: 17px; color: var(--accent);
    text-transform: uppercase; letter-spacing: 0.5px;
  }
  .holder-role { font-size: 12px; color: var(--ink-soft); }
  .contact-rule {
    position: absolute; left: 28px; top: 222px; width: 180px; height: 1px; background: var(--accent);
  }
  .contacts {
    position: absolute; left: 28px; top: 230px; list-style: none;
    font-size: 11.5px; line-height: 19px; color: var(--ink);
  }
  .contacts li { display: flex; align-items: center; gap: 8px; }
  .contacts svg { width: 10px; height: 10px; fill: var(--accent); }
  /* Back */
  .texture {
    position: absolute; inset: 0;
    background: linear-gradient(120deg, #0c0c0c 0%, #181818 45%, #2e2e2e 100%);
  }
  .back-brand {
    position: absolute; left: 330px; top: 120px;
    display: flex; align-items: center; gap: 10px;
  }
  .back-brand .brand-dot { width: 22px; height: 22px; }
  .back-brand .brand-name { font-size: 22px; color: var(--accent); font-weight: 700; letter-spacing: 1.5px; }
</style>
</head>
<body>
<main class="stage">
  <section class="card card-front" aria-label="Business card front">
    <div class="brand">
      <span class="brand-dot"></span>
      <span class="brand-name">QUARROW</span>
    </div>
    <div class="brand-tagline">Signal Instruments</div>
    <div class="divider"></div>
    <p class="address">1180 Larkmere Cove Dr<br>Halvern Bay CA 90417</p>
    <div class="holder">
      <p class="holder-name">Dorian Velcott</p>
      <p class="holder-role">President</p>
    </div>
    <div class="contact-rule"></div>
    <ul class="contacts">
      <li><svg viewBox="0 0 10 10"><path d="M2 0h2l1 3-1.5 1a6 6 0 0 0 2.5 2.5L7 5l3 1v2a2 2 0 0 1-2 2A8 8 0 0 1 0 2a2 2 0 0 1 2-2z"/></svg>555-013-2870</li>
      <li><svg viewBox="0 0 10 10"><path d="M0 2h10v6H0zM0 2l5 3.5L10 2"/></svg>d.velcott@quarrowsignal.com</li>
      <li><svg viewBox="0 0 10 10"><circle cx="5" cy="5" r="5"/></svg>www.quarrowsignal.com</li>
    </ul>
  </section>

  <section class="card card-back" aria-label="Business card back">
    <div class="texture" role="img" aria-label="Raised gloss texture of repeated brand marks on black"></div>
    <div class="back-brand">
      <span class="brand-dot"></span>
      <span class="brand-name">QUARROW</span>
    </div>
  </section>
</main>
</body>
</html>
```